Birchline Septic Solutions

Would like to see some single sided ones but would also like to see some double sided with one sided only being the logo. Owners name is Colin Vandro. Phone number is 555-214-0387
Services are pumping, inspections, installs, and repairs

Contact Information for Business Card

555-241-0387 Colin Vandro Harlow Springs, OH

```html
<!DOCTYPE html>
<html lang="en">
<head>
<meta charset="utf-8">
<title>Birchline Septic Solutions – Business Card</title>
<link rel="stylesheet" href="https://fonts.googleapis.com/css2?family=Open+Sans:wght@400;600;700&display=swap">
<style>
  :root {
    --page-bg: #d9dce1;
    --card-dark: #141518;
    --card-mid: #1f2024;
    --card-light: #3b3c41;
    --ridge: #26272b;
    --teal: #2aa89a;
    --white: #f1f1f4;
    --muted: #9a9cb0;
  }
  * { margin: 0; padding: 0; box-sizing: border-box; }
  html, body {
    width: 1200px;
    height: 779px;
    overflow: hidden;
    background: var(--page-bg);
    font-family: "Open Sans", Arial, sans-serif;
  }
  .business-card {
    position: absolute;
    left: 50px;
    top: 87px;
    width: 1100px;
    height: 604px;
    overflow: hidden;
    background:
      radial-gradient(ellipse 60% 70% at 18% 20%, var(--card-light) 0%, rgba(59,60,65,0) 70%),
      linear-gradient(160deg, var(--card-mid) 0%, var(--card-dark) 55%, var(--card-mid) 100%);
    box-shadow: 0 12px 30px rgba(0,0,0,0.25);
  }
  .brand-name {
    position: absolute;
    left: 46px;
    top: 150px;
    width: 480px;
    color: var(--white);
    font-weight: 700;
    font-size: 50px;
    line-height: 1.15;
    letter-spacing: 1px;
  }
  .ridge-scene {
    position: absolute;
    right: 5px;
    bottom: 0;
    width: 760px;
    height: 205px;
    background: linear-gradient(180deg, rgba(38,39,43,0) 0%, var(--ridge) 100%);
    opacity: 0.7;
  }
  .contact-block {
    position: absolute;
    right: 40px;
    top: 26px;
    text-align: right;
    color: var(--white);
  }
  .owner-name {
    font-size: 48px;
    font-weight: 700;
    line-height: 1.2;
  }
  .owner-name .first-name { color: var(--teal); }
  .location, .phone {
    font-size: 29px;
    font-weight: 400;
    line-height: 1.4;
    letter-spacing: 0.5px;
  }
  .phone { display: flex; align-items: center; justify-content: flex-end; gap: 12px; }
  .phone-icon { width: 24px; height: 24px; }
  .accent-bar {
    position: absolute;
    right: 0;
    top: 38px;
    width: 23px;
    height: 118px;
    background: var(--teal);
  }
  .services {
    position: absolute;
    left: 46px;
    top: 380px;
  }
  .services-heading {
    color: var(--teal);
    font-size: 27px;
    font-weight: 700;
    letter-spacing: 0.5px;
    margin-bottom: 2px;
    opacity: 0.85;
  }
  .services-list { list-style: none; }
  .services-list li {
    display: flex;
    align-items: center;
    gap: 14px;
    color: var(--muted);
    font-size: 29px;
    line-height: 36px;
  }
  .services-list li::before {
    content: "";
    width: 15px;
    height: 15px;
    border-radius: 50%;
    background: var(--teal);
    opacity: 0.7;
  }
  .services-list li.plain::before { visibility: hidden; }
</style>
</head>
<body>
  <div class="business-card">
    <div class="brand-name">Birchline<br>Septic Solutions</div>

    <div class="ridge-scene" role="img" aria-label="Faint mountain and pine tree silhouette"></div>

    <div class="contact-block">
      <div class="owner-name"><span class="first-name">Colin</span> Vandro</div>
      <div class="location">Harlow Springs, OH</div>
      <div class="phone">555-241-0387
        <svg class="phone-icon" viewBox="0 0 24 24" aria-hidden="true">
          <path fill="var(--teal)" d="M6.6 10.8c1.4 2.8 3.8 5.1 6.6 6.6l2.2-2.2c.3-.3.7-.4 1-.2 1.1.4 2.3.6 3.6.6.6 0 1 .4 1 1V20c0 .6-.4 1-1 1C10.6 21 3 13.4 3 4c0-.6.4-1 1-1h3.5c.6 0 1 .4 1 1 0 1.3.2 2.5.6 3.6.1.3 0 .7-.2 1z"/>
          <path fill="none" stroke="var(--teal)" stroke-width="1.8" stroke-linecap="round" d="M14 3.5a7 7 0 0 1 6.5 6.5M14 7a3.5 3.5 0 0 1 3 3"/>
        </svg>
      </div>
    </div>
    <div class="accent-bar"></div>

    <div class="services">
      <div class="services-heading">SERVICES</div>
      <ul class="services-list">
        <li>Pumping</li>
        <li>Inspections</li>
        <li>Installs</li>
        <li class="plain">and Repairs</li>
      </ul>
    </div>
  </div>
</body>
</html>
```